Brisk. Technology Logistics Software platform.

A modern looking and feeling website for a logistics software platform.
We connect retailers or wholesale parcel distributors to worldwide delivery solutions.
Methods tend to be road and air transport to final mile courier companies and post offices all over the world.
Our platform is for ecommerce distribution. A customer uses BRISK to enable them to connect to worldwide companies who will track and trace the delivery of their goods.

Target Market(s)

Onllne retailers. Markert Places such as Vendora and Tradelo. Wholesale third party logistics and packaging companies. Delivery companies based in the UK looking to expand overseas.

Number of Pages Required

5+ page

Font styles to use
Sans Serif

Colors
aaaaaa
dbdbdb
e6e6e6
c4c4c4
cbcbcb
c9c9c9
ec1f27
3176b5
0355a3

Requirements
Must have
• Landing Page.
• What we do.
• Who we are.
• Modules.
• Testimonies (password protected)
• Contact us.
• Interactive for mobile operating systems.
• Scrolling website.
• Short stock video showing on key pages.
• Very well polished fonts and buttons. A sharp and well executed website is required.
• Simplicity in feeling.
• To the point on message.
• Refined wording and copyrighting / messaging
• A link to our sub brand and product Brisk Parcels
• Capture interest so people read further.
Nice to have
• A polished video to explain what we do on landing page. Clipmarrow.net have some good options but not sure how professional they will look.
Should not have
• Bad graphics and colours.
• Not lots of clicks. Less as possible
• Complex message

```html
<!DOCTYPE html>
<html lang="en">
<head>
<meta charset="utf-8">
<title>Brisk. Technology</title>
<link href="https://fonts.googleapis.com/css2?family=Open+Sans:wght@400;600;700&display=swap" rel="stylesheet">
<style>
  :root {
    --page-bg: #d3d3d3;
    --white: #ffffff;
    --brand-red: #e2172b;
    --brand-navy: #0b3d8c;
    --nav-active: #0355a3;
    --text-dark: #444444;
    --text-nav: #555555;
    --footer-bg: #2a2a2a;
    --footer-text: #d8d8d8;
  }
  * { margin: 0; padding: 0; box-sizing: border-box; }
  html, body { width: 848px; height: 1200px; overflow: hidden; }
  body { background: var(--page-bg); font-family: "Open Sans", sans-serif; position: relative; }

  .panel { position: absolute; left: 27px; width: 795px; overflow: hidden; }

  /* Landing panel */
  .landing { top: 26px; height: 408px; }
  .landing-media {
    position: absolute; inset: 0;
    background: linear-gradient(135deg, #7b8797 0%, #5e6a7c 35%, #4a5566 60%, #6f7a88 100%);
  }
  .landing-shade { position: absolute; inset: 0; background: rgba(40,48,62,0.35); }
  .landing-logo {
    position: absolute; left: 331px; top: 16px; width: 132px; height: 54px;
    background: var(--white); border-radius: 2px;
    display: flex; align-items: center; justify-content: center;
    color: var(--brand-red); font-weight: 700; font-size: 17px;
  }
  .play-button { position: absolute; left: 381px; top: 121px; }
  .landing-title {
    position: absolute; left: 0; right: 0; top: 163px; text-align: center;
    color: var(--white); font-weight: 700; font-size: 32px; letter-spacing: 0.3px;
  }
  .landing-copy {
    position: absolute; left: 0; right: 0; top: 206px; text-align: center;
    color: var(--white); font-weight: 600; font-size: 11px; line-height: 21px;
  }
  .landing-footer {
    position: absolute; left: 0; right: 0; bottom: 0; height: 37px;
    background: rgba(30,30,30,0.88);
  }

  .copyright { position: absolute; left: 95px; color: var(--footer-text); font-size: 7.5px; }
  .social { position: absolute; left: 669px; display: flex; gap: 10px; }
  .social span { width: 10px; height: 10px; border-radius: 50%; background: #bfbfbf; display: block; }

  /* Site panel */
  .site { top: 456px; height: 720px; background: var(--white); }
  .site-header { position: absolute; left: 0; right: 0; top: 0; height: 53px; background: var(--white); }
  .site-logo {
    position: absolute; left: 95px; top: 17px;
    color: var(--brand-red); font-weight: 700; font-size: 17px;
  }
  .main-nav { position: absolute; top: 20px; font-size: 9.5px; color: var(--text-nav); }
  .main-nav a { position: absolute; white-space: nowrap; color: inherit; text-decoration: none; }
  .main-nav a.active { color: var(--nav-active); }

  .hero { position: absolute; left: 0; right: 0; top: 53px; height: 353px; }
  .hero-media {
    position: absolute; inset: 0;
    background: linear-gradient(160deg, #9fb3cc 0%, #6f8fbf 35%, #4f74ad 60%, #8aa0c0 100%);
  }
  .hero-title {
    position: absolute; left: 0; right: 0; top: 120px; text-align: center;
    color: var(--white); font-weight: 700; font-size: 38px; line-height: 44px;
    text-shadow: 0 1px 3px rgba(0,0,0,0.35);
  }
  .hero-sub {
    position: absolute; left: 0; right: 0; top: 166px; text-align: center;
    color: var(--white); font-weight: 600; font-size: 21px; line-height: 28px;
    text-shadow: 0 1px 3px rgba(0,0,0,0.35);
  }

  .welcome { position: absolute; left: 0; right: 0; top: 448px; text-align: center; }
  .welcome h1 { color: var(--brand-red); font-weight: 600; font-size: 27px; line-height: 36px; }
  .welcome p {
    color: var(--text-dark); font-size: 9.8px; line-height: 17px;
    width: 610px; margin: 0 auto;
  }
  .welcome .intro { margin-top: 10px; }
  .welcome .support { margin-top: 17px; }
  .ensuring {
    position: absolute; left: 0; right: 0; top: 588px;
    display: flex; justify-content: center; align-items: center; gap: 6px;
    color: var(--text-dark); font-size: 9.8px;
  }
  .ensuring .lead { margin-right: 6px; }
  .ensuring .tail { margin-left: 4px; }
  .btn {
    background: var(--brand-navy); color: var(--white); font-weight: 600;
    font-size: 9.8px; padding: 0 12px; height: 26px; line-height: 26px; border-radius: 2px;
  }

  .site-footer { position: absolute; left: 0; right: 0; bottom: 0; height: 53px; background: var(--footer-bg); }
  .footer-links { position: absolute; left: 95px; top: 12px; color: var(--footer-text); font-size: 7.5px; }
  .footer-links span { margin: 0 5px; }
</style>
</head>
<body>

<section class="panel landing">
  <div class="landing-media" role="img" aria-label="Aerial view of a logistics warehouse with lorries at loading bays"></div>
  <div class="landing-shade"></div>
  <div class="landing-logo">Brisk. Technology</div>
  <svg class="play-button" width="32" height="32" viewBox="0 0 32 32" aria-hidden="true">
    <circle cx="16" cy="16" r="16" fill="#ffffff"/>
    <circle cx="16" cy="16" r="10" fill="none" stroke="#2b2b2b" stroke-width="1.4"/>
    <path d="M13 10.5 L21.5 16 L13 21.5 Z" fill="#2b2b2b"/>
  </svg>
  <h2 class="landing-title">BRISK.TECHNOLOGY... &nbsp;OUR FOCUS</h2>
  <div class="landing-copy">
    <p>We provide advanced software solutions to ensure you connect with global e commerce delivery carriers</p>
    <p>You can manage your Global Delivery Network in one place, with</p>
    <p>Our software will enable you monitor the productivity and reporting of your e commerce deliveries</p>
    <p>Manage your carriers, your delivery speeds, and your costs</p>
  </div>
  <footer class="landing-footer">
    <p class="copyright" style="top:14px">Copyright &copy; 2018 Brisk Technology. &nbsp;All rights reserved.</p>
    <div class="social" style="top:14px"><span></span><span></span></div>
  </footer>
</section>

<section class="panel site">
  <header class="site-header">
    <div class="site-logo">Brisk. Technology</div>
    <nav class="main-nav">
      <a class="active" style="left:459px">Home</a>
      <a style="left:505px">Solutions</a>
      <a style="left:563px">Testimonial Login</a>
      <a style="left:655px">Contact Us</a>
    </nav>
  </header>

  <div class="hero">
    <div class="hero-media" role="img" aria-label="Blue-toned modern factory floor with automated parcel handling lines"></div>
    <h2 class="hero-title">BRISK.</h2>
    <p class="hero-sub">Technology and Parcel Solutions Built To<br>Help Develop &amp; Manage Your Global Delivery Network</p>
  </div>

  <div class="welcome">
    <h1>Welcome to Brisk</h1>
    <p class="intro">Working closely with Ecommerce, Brisk. Technology have developed solutions purely focused on delivering what’s required within the global delivery marketplace. Meeting all needs and more for Retailers and Global Delivery Solution providers</p>
    <p class="support">Allowing customers to grow at a fast pace; most importantly providing tools to help them manage their global delivery network supported by “Dynamic Real Time Visibility” management tools.</p>
  </div>

  <div class="ensuring">
    <span class="lead">Ensuring</span>
    <span class="btn">BRISK PARCEL</span>
    <span class="btn">BRISK TECHNOLOGY</span>
    <span class="tail">solutions evolve to suit our customers business requirements.</span>
  </div>

  <footer class="site-footer">
    <p class="footer-links">Home<span>|</span>Solutions<span>|</span>Testimonial Login<span>|</span>Contact Us</p>
    <p class="copyright" style="top:31px">Copyright &copy; 2018 Brisk Technology. &nbsp;All rights reserved.</p>
    <div class="social" style="top:22px"><span></span><span></span></div>
  </footer>
</section>

</body>
</html>
```